Business Card and Letterhead for Pimlu - modern real estate business

I need a double sided business card design for Pimlu. Please see business card brief here https://files.trelvonadocs.com/sheet/r/7QzTmWbaXLJnoPEd-kRyUgFhHsstbvCe2qfoMxDa_pz/view?mode=shared

Please feel free to design the business cards however you feel best. I am happy to give some creative freedoms and then provide feedback from there.

Please then also create a letterhead to match the business card design

Colors

Designer to choose colors to be used in the design.

Requirements
Must have
• Must be a modern, elegant business card which looks very professional

```html
<!DOCTYPE html>
<html lang="en">
<head>
<meta charset="UTF-8">
<title>Pimlu – Business Card</title>
<link href="https://fonts.googleapis.com/css2?family=Montserrat:wght@400;500;700&display=swap" rel="stylesheet">
<style>
  :root{
    --page-bg:#e9e7e4;
    --card-black:#1f1d1e;
    --card-white:#ffffff;
    --brand-red:#e5141c;
    --ink:#1a1a1a;
    --rule:#555555;
    --photo-top:#d9d9d9;
    --photo-bottom:#4a4a4c;
  }
  *{margin:0;padding:0;box-sizing:border-box}
  html,body{width:1200px;height:800px;overflow:hidden}
  body{
    background:var(--page-bg);
    font-family:"Montserrat",Arial,sans-serif;
    display:flex;align-items:center;justify-content:center;gap:40px;
  }
  .card{
    width:540px;height:310px;position:relative;overflow:hidden;
    box-shadow:0 6px 18px rgba(0,0,0,.18);
  }
  /* front */
  .card--front{background:var(--card-black);display:flex;align-items:center;justify-content:center}
  .brand-name{
    font-weight:700;color:var(--brand-red);letter-spacing:.06em;text-transform:uppercase;line-height:1;
  }
  .card--front .brand-name{font-size:64px}
  /* back */
  .card--back{background:var(--card-white)}
  .agent-photo{
    position:absolute;left:0;top:0;width:250px;height:100%;
    background:linear-gradient(180deg,var(--card-white) 0%,var(--photo-top) 35%,var(--photo-bottom) 100%);
  }
  .details{
    position:absolute;left:270px;right:26px;top:58px;text-align:center;
  }
  .card--back .brand-name{font-size:44px;margin-bottom:14px}
  .agent-name{
    color:var(--brand-red);font-weight:700;font-size:19px;letter-spacing:.04em;text-transform:uppercase;
  }
  .agent-title{color:var(--ink);font-size:13px;font-weight:500;margin-top:3px}
  .icon-rule{
    display:flex;align-items:center;justify-content:center;gap:4px;margin:10px auto 6px;width:150px;
  }
  .icon-rule::before,.icon-rule::after{content:"";flex:1;height:1px;background:var(--rule)}
  .contact-list{list-style:none;color:var(--ink);font-size:13.5px;line-height:1.35}
  .address-band{
    position:absolute;left:250px;right:0;bottom:0;height:34px;
    background:var(--brand-red);border-top:3px solid var(--ink);
    color:var(--card-white);font-size:12.5px;font-weight:500;
    display:flex;align-items:center;padding-left:18px;
  }
</style>
</head>
<body>
  <section class="card card--front" aria-label="Business card front">
    <span class="brand-name">Pimlu</span>
  </section>

  <section class="card card--back" aria-label="Business card back">
    <div class="agent-photo" role="img" aria-label="Portrait photo of the agent in a dark suit"></div>

    <div class="details">
      <div class="brand-name">Pimlu</div>
      <div class="agent-name">Dean Marlow</div>
      <div class="agent-title">Licenced Real Estate Agent</div>

      <div class="icon-rule" aria-hidden="true">
        <svg width="16" height="16" viewBox="0 0 16 16"><circle cx="8" cy="8" r="8" fill="#e5141c"/><path d="M5.2 4.3l1.3-.3.8 1.8-.9.7c.5 1 1.2 1.7 2.2 2.2l.7-.9 1.8.8-.3 1.3c-3.2.3-5.9-2.4-5.6-5.6z" fill="#fff"/></svg>
        <svg width="16" height="16" viewBox="0 0 16 16"><circle cx="8" cy="8" r="8" fill="#e5141c"/><rect x="4" y="5.2" width="8" height="5.6" fill="#fff"/><path d="M4 5.4l4 3 4-3" fill="none" stroke="#e5141c" stroke-width=".9"/></svg>
        <svg width="16" height="16" viewBox="0 0 16 16"><circle cx="8" cy="8" r="8" fill="#e5141c"/><g fill="none" stroke="#fff" stroke-width=".9"><circle cx="8" cy="8" r="3.8"/><ellipse cx="8" cy="8" rx="1.6" ry="3.8"/><path d="M4.2 8h7.6"/></g></svg>
      </div>

      <ul class="contact-list">
        <li>0400 555 182</li>
        <li>dean@pimlu.com</li>
        <li>www.pimlu.com</li>
      </ul>
    </div>

    <div class="address-band">PO Box 1180, Larkfield NSW 2790</div>
  </section>
</body>
</html>
```